Corvane Capital Business Cards

These are professional business cards that are for my family office.
Put fake emails and phone numbers as of now until I finalize those components. This family office controls my families investments, assets, and future. The cards should be professional.
..
.
.
.
I just uploaded another variation of a logo I would like to see as a business card to I am inbeteen which logo to use

Target Market(s)

business

Industry/Entity Type

business

Contact Information for Business Card

Professional, wealth related, finance related.

Requirements
Must have
• Logo

```html
<!DOCTYPE html>
<html lang="en">
<head>
<meta charset="UTF-8">
<title>Corvane Capital Business Cards</title>
<link rel="stylesheet" href="https://fonts.googleapis.com/css2?family=Cinzel:wght@500&family=Montserrat:wght@400;700&family=Nunito:wght@400&display=swap">
<style>
  :root {
    --stage: #3a3a3a;
    --navy: #1a1f2e;
    --paper: #ffffff;
    --grey: #a9a9a9;
    --ink: #555a63;
    --white: #ffffff;
  }
  * { margin: 0; padding: 0; box-sizing: border-box; }
  html, body { width: 1200px; height: 689px; overflow: hidden; }
  body { background: var(--stage); position: relative; }

  .card {
    position: absolute;
    width: 525px;
    height: 300px;
    border-radius: 18px;
    overflow: hidden;
    box-shadow: 0 12px 30px rgba(0,0,0,0.35);
  }
  .brand-name {
    font-family: "Cinzel", serif;
    font-weight: 500;
    white-space: nowrap;
  }

  /* Front */
  .card-front {
    left: 50px;
    top: 195px;
    background: var(--navy);
  }
  .front-ring {
    position: absolute;
    left: 217px;
    top: 62px;
    width: 92px;
    height: 92px;
    border: 3px solid var(--white);
    border-radius: 50%;
  }
  .card-front .brand-name {
    position: absolute;
    left: 0;
    right: 0;
    top: 176px;
    text-align: center;
    color: var(--white);
    font-size: 34px;
    letter-spacing: 1px;
  }

  /* Back */
  .card-back {
    left: 625px;
    top: 195px;
    background: var(--paper);
  }
  .card-back .brand-name {
    position: absolute;
    left: 34px;
    top: 48px;
    color: var(--navy);
    font-size: 25px;
  }
  .side-bar {
    position: absolute;
    left: 38px;
    top: 116px;
    width: 8px;
    height: 150px;
    background: var(--grey);
  }
  .contact-list {
    position: absolute;
    left: 56px;
    top: 112px;
    list-style: none;
    font-family: "Nunito", sans-serif;
    font-size: 13px;
    color: var(--ink);
    line-height: 1.35;
  }
  .contact-list li {
    display: flex;
    align-items: flex-start;
    gap: 10px;
    margin-bottom: 3px;
  }
  .contact-list svg {
    width: 13px;
    height: 13px;
    flex: none;
    margin-top: 3px;
    fill: var(--navy);
  }
  .emblem {
    position: absolute;
    left: 0;
    top: 0;
    width: 525px;
    height: 300px;
  }
  .holder {
    position: absolute;
    right: 24px;
    top: 124px;
    color: var(--white);
    text-align: right;
    white-space: nowrap;
  }
  .holder-name {
    font-family: "Montserrat", sans-serif;
    font-weight: 700;
    font-size: 21px;
    letter-spacing: 0.5px;
  }
  .holder-role {
    font-family: "Montserrat", sans-serif;
    font-weight: 400;
    font-size: 13px;
    margin-top: 2px;
  }
</style>
</head>
<body>
  <section class="card card-front">
    <div class="front-ring"></div>
    <div class="brand-name">Corvane Capital</div>
  </section>

  <section class="card card-back">
    <svg class="emblem" viewBox="0 0 525 300">
      <circle cx="420" cy="150" r="135" fill="var(--navy)"/>
      <path d="M 496 18 A 152 152 0 0 0 304 52" fill="none" stroke="var(--navy)" stroke-width="6"/>
      <path d="M 304 248 A 152 152 0 0 0 472 293" fill="none" stroke="var(--navy)" stroke-width="6"/>
      <g fill="var(--grey)">
        <circle cx="288" cy="74" r="10"/>
        <circle cx="273" cy="111" r="10"/>
        <circle cx="268" cy="150" r="10"/>
        <circle cx="273" cy="189" r="10"/>
        <circle cx="288" cy="226" r="10"/>
      </g>
    </svg>

    <div class="brand-name">Corvane Capital</div>
    <div class="side-bar"></div>
    <ul class="contact-list">
      <li>
        <svg viewBox="0 0 24 24"><path d="M12 2a7 7 0 0 0-7 7c0 5 7 13 7 13s7-8 7-13a7 7 0 0 0-7-7zm0 9.5A2.5 2.5 0 1 1 12 6.5a2.5 2.5 0 0 1 0 5z"/></svg>
        <span>423 Street Address Here, City<br>State &amp; Country, ZIP Code</span>
      </li>
      <li>
        <svg viewBox="0 0 24 24"><path d="M6.6 10.8a15 15 0 0 0 6.6 6.6l2.2-2.2a1 1 0 0 1 1-.25 11.4 11.4 0 0 0 3.6.57 1 1 0 0 1 1 1V20a1 1 0 0 1-1 1A17 17 0 0 1 3 4a1 1 0 0 1 1-1h3.5a1 1 0 0 1 1 1c0 1.25.2 2.45.57 3.57a1 1 0 0 1-.25 1z"/></svg>
        <span>(123) 456-7890</span>
      </li>
      <li>
        <svg viewBox="0 0 24 24"><path d="M7 1h10a2 2 0 0 1 2 2v18a2 2 0 0 1-2 2H7a2 2 0 0 1-2-2V3a2 2 0 0 1 2-2zm0 3v14h10V4zm5 15.5a1 1 0 1 0 0 2 1 1 0 0 0 0-2z"/></svg>
        <span>(123) 456-7890</span>
      </li>
      <li>
        <svg viewBox="0 0 24 24"><path d="M6 2h12v5H6zM4 8h16a2 2 0 0 1 2 2v7h-4v5H6v-5H2v-7a2 2 0 0 1 2-2zm4 8v4h8v-4z"/></svg>
        <span>(123) 456-7890</span>
      </li>
      <li>
        <svg viewBox="0 0 24 24"><path d="M2 5h20v14H2zm2 2v.5l8 5 8-5V7zm0 3v7h16v-7l-8 5z"/></svg>
        <span>info@yourwebsitehere.com</span>
      </li>
      <li>
        <svg viewBox="0 0 24 24"><path d="M12 2a10 10 0 1 0 0 20 10 10 0 0 0 0-20zm0 2c.9 0 2.2 1.8 2.8 5H9.2C9.8 5.8 11.1 4 12 4zM4.3 11h3.8a18 18 0 0 0 0 2H4.3a8 8 0 0 1 0-2zm1 4h3.1c.3 1.6.8 3 1.4 4A8 8 0 0 1 5.3 15zm3.1-6H5.3a8 8 0 0 1 4.5-4c-.6 1-1.1 2.4-1.4 4zM12 20c-.9 0-2.2-1.8-2.8-5h5.6c-.6 3.2-1.9 5-2.8 5zm3.1-7H8.9a16 16 0 0 1 0-2h6.2a16 16 0 0 1 0 2zm-.9 6c.6-1 1.1-2.4 1.4-4h3.1a8 8 0 0 1-4.5 4zm1.7-6a18 18 0 0 0 0-2h3.8a8 8 0 0 1 0 2zm-.3-4c-.3-1.6-.8-3-1.4-4a8 8 0 0 1 4.5 4z"/></svg>
        <span>yourwebsitehere.com</span>
      </li>
    </ul>

    <div class="holder">
      <div class="holder-name">DANIEL HARPER</div>
      <div class="holder-role">Founder &amp; CEO</div>
    </div>
  </section>
</body>
</html>
```